2-Page Flyer for the Information Session about the Quiet Pathfinder Course

This is a flyer to announce/advertise an evening Information Session about the Quiet Pathfinder Course. This Program aims at mindfully rethinking and redesigning work (and life) for people who feel stuck or not entirely satisfied with their work and/or life (please see draft flyer attached for more details). This Program is property of Bright Meadow, a company that uses a combination of Mindfulness, Design, and Entrepreneurship to help people achieve greater happiness (in their work and lives).

Target Market(s)

People who feel stuck or not entirely satisfied with their work and/or life (please see draft flyer attached for more details)

Font styles to use
Serif
Sans Serif

Colors
ffffff
f37122
33a6d7
acd037

Requirements
Must have
• All of what I will say below is suggestive (I’m not a design expert), and I’m open to divert from it, if it makes sense and feels more interesting.
• I thought initially of a 2-page flyer (please see draft flyer attached). The first page could help people grasp the essence of the event quickly (in 1 or 2 minutes), and then, if they are interested/motivated, they would continue reading through page 2, which has more info about the Program in itself.
• Potential Structure
• Page 1
• . About the Information Session on the Quiet Pathfinder Course
• . Visible Date & Time, Contacts, Venue (and other relevant info)
• . About me (the facilitator)
• Page 2
• . About the Quiet Pathfinder Course
• I include a Powerpoint draft of the flyer with the content. The design is rudimentary and precarious from an aesthetics/organization point of view, and this is mainly where I need help (and maybe in other aspects too!).
• On the flyer, I would like to include:
• . A photo of myself (I attach 1 picture).
• . 1 or 2 beautiful-nature photos (cropped or full). One may have to do with looking at the sky, dreaming, and imagining a new work and life (2 photos with sky and clouds attached). The other has to do with walking the transformation journey (the photo with the person walking through the forest path).
• . bright meadow logo or logos (there are two slightly different ones, that can be used for different purposes). For the first page, I would like the bright meadow logo that has "bright meadow" written on the bottom, with the saying "Stillness, Craft and Venture for Bright Meadow" beneath. This is the main logo. For the 2nd page, you can choose the logo that adapts better.
• - Where it says the "the way out is in" it would be great to have a similar font to the one I attach (see file "Font_the_way_out_is_in.png" and Ankecallig-fg.ttf
Nice to have
• In terms of colours, I would not divert much from the logo colours (and of course white and black). I would like the flyer to be quite white. Almost like fairy-tale white: the white horse, the white snow, the white of the stars, the white heaven. White could be the base colour. White means peace, tranquillity, calm contentment, a smile.
• And then use the other colours. The green of the mindfulness. The blue of the sky, the dreams. And the orange of the sun, the energy, the fire, the action. And maybe the black for text.
• Where it says the "the way out is in" it would be great to have a similar font to the one I attach (see file "Font_the_way_out_is_in".
• I would like this flyer to be a piece of art, in every possible way. Simple, beautiful, ease, light, peaceful, calm happy. Just like the Quiet Pathfinder Course and bright meadow Company that I am creating intends to be. The mission of this Program and Company is to be a designer, a painter (a Picasso) of happier and more fulfilling human lives.
• I am very much looking forward to seeing your proposal(s).

```html
<!DOCTYPE html>
<html lang="en">
<head>
<meta charset="utf-8">
<title>Quiet Pathfinder Course – Information Session Flyer</title>
<link href="https://fonts.googleapis.com/css2?family=Roboto:ital,wght@0,400;0,500;0,700;1,400;1,700&family=Roboto+Condensed:wght@400;700;900&family=Dancing+Script:wght@600&display=swap" rel="stylesheet">
<style>
:root{
  --orange:#f37122;
  --orange-soft:#ee8a3a;
  --blue:#33a6d7;
  --blue-deep:#1f5fbf;
  --green:#acd037;
  --grey:#9a9a9a;
  --ink:#111;
  --text:#222;
  --white:#fff;
  --stage:#f6f6f8;
}
*{box-sizing:border-box;margin:0;padding:0}
html,body{width:1200px;height:1200px;overflow:hidden;background:var(--stage)}
body{position:relative;font-family:"Roboto",Arial,sans-serif;color:var(--text)}
.page{position:absolute;top:254px;width:480px;height:678px;background:var(--white);overflow:hidden}
.page--front{left:94px}
.page--back{left:643px}
.abs{position:absolute}
p{font-size:7.6px;line-height:10.4px;text-align:justify}

/* front */
.hero{left:0;top:0;width:480px;height:291px;
  background:linear-gradient(180deg,#7fb4e3 0%,#c9dcef 28%,#9fb2bd 48%,#7e9a80 66%,#6f8f5c 82%,#8d9c74 100%)}
.hero-band{left:0;top:291px;width:480px;height:9px;background:var(--orange)}
.title{font-family:"Roboto Condensed",sans-serif;font-weight:900;color:var(--ink);left:95px;width:290px;text-align:center;line-height:1}
.title--a{top:44px;font-size:66px;letter-spacing:4px}
.title--b{top:108px;font-size:30px;letter-spacing:3.4px}
.title--c{top:136px;font-size:56px;letter-spacing:3px}
.session-tag{left:95px;top:190px;width:290px;height:22px;background:var(--orange);border:1.5px solid var(--white);
  color:var(--white);font-family:"Roboto Condensed",sans-serif;font-weight:700;font-size:16px;letter-spacing:5.2px;text-align:center;line-height:19px}
.when{left:95px;width:290px;text-align:center;font-family:"Roboto Condensed",sans-serif;font-weight:700;color:var(--ink)}
.when--date{top:224px;font-size:20px}
.when--time{top:246px;font-size:20px}
.h-section{font-family:"Roboto Condensed",sans-serif;font-weight:700;font-size:12px;letter-spacing:.2px}
.h-section--orange{color:var(--orange)}
.h-section--blue{color:var(--blue)}
.col-info{left:36px;top:314px;width:191px}
.col-who{left:256px;top:314px;width:190px}
.col-info .h-section,.col-who .h-section{margin-bottom:2px}
.portrait{left:32px;top:373px;width:113px;height:176px;
  background:linear-gradient(180deg,#e9eef1 0%,#c9b3a6 30%,#3e4a58 62%,#2b3542 100%)}
.bio-box{left:32px;top:428px;width:420px;height:121px;background:var(--blue)}
.portrait{z-index:2}
.bio-text{left:153px;top:436px;width:290px;z-index:3}
.bio-text p{color:#10263a;font-size:7.4px;line-height:10.4px}
.facilitator{left:153px;top:414px;white-space:nowrap;font-size:11px}
.facilitator .role{color:var(--green);font-size:8px}
.facilitator .name{font-family:"Roboto Condensed",sans-serif;font-weight:700;color:var(--ink)}
.facilitator .post{font-style:italic;font-size:7px;color:var(--ink)}
.link-bar{left:98px;top:550px;width:283px;height:17px;background:var(--orange);color:var(--white);font-size:9px;text-align:center;line-height:17px}
.link-bar em{font-weight:700}
.brand{display:flex;align-items:center;gap:8px}
.brand-dot{width:44px;height:44px;border-radius:50%;background:var(--orange);flex:none}
.brand-name{font-family:"Roboto",sans-serif;font-weight:400;color:var(--orange);line-height:.95}
.brand--front{left:32px;top:603px}
.brand--front .brand-name{font-size:25px}
.divider{left:225px;top:597px;width:1px;height:61px;background:var(--orange)}
.booking{left:232px;top:601px;width:215px;color:var(--ink)}
.booking h3{font-family:"Roboto Condensed",sans-serif;font-weight:700;font-size:13px;text-align:center}
.booking .contact-row{display:flex;justify-content:space-between;font-size:10px;margin-top:3px}
.booking .note{font-size:6px;font-style:italic;text-align:right;margin-top:1px}
.booking .venue{font-size:9.4px;margin-top:5px;text-align:center}

/* back */
.brand--back{left:336px;top:13px}
.brand--back .brand-dot{width:36px;height:36px}
.brand--back .brand-name{font-size:15px}
.what-band{left:0;top:55px;width:480px;height:65px;background:linear-gradient(90deg,var(--blue-deep) 0%,#2a73cf 60%,#4b93dc 100%);padding:7px 30px 0 29px;color:var(--white)}
.what-band h2{font-family:"Roboto Condensed",sans-serif;font-weight:700;font-size:13px;margin-bottom:4px}
.what-band p{font-size:7.4px;line-height:9.8px;color:var(--white)}
.cycle{left:0;top:120px;width:260px;height:180px}
.cycle-label{font-size:6.8px;font-weight:500;color:var(--ink);text-align:center;line-height:8px}
.program{left:258px;top:148px;width:193px}
.h-block{font-family:"Roboto Condensed",sans-serif;font-weight:700;font-size:13px;margin-bottom:5px}
.program p{margin-bottom:10px}
.why{left:30px;top:295px;width:192px}
.how{left:250px;top:295px;width:201px}
.why .h-block,.how .h-block{color:var(--orange)}
.program .h-block{color:var(--blue)}
.steps{list-style:none;margin-top:10px}
.steps li{font-size:7.6px;line-height:10.4px;padding-left:11px;position:relative}
.steps li .num{position:absolute;left:0;top:1.5px;width:7.5px;height:7.5px;border-radius:50%;color:var(--white);font-size:5.5px;line-height:7.5px;text-align:center;font-weight:700}
.steps--why .num{background:var(--orange)}
.steps--how .num{background:var(--green)}
.how .format{margin-top:10px;text-align:left}
.forest{left:0;top:461px;width:480px;height:177px;
  background:radial-gradient(ellipse 16% 30% at 50% 38%,#c9c48e 0%,#6f6a3a 40%,transparent 100%),linear-gradient(90deg,#2d2415 0%,#4a3a22 30%,#3b3220 50%,#4a3a22 70%,#2a2214 100%)}
.motto{left:0;top:593px;width:480px;text-align:center;font-family:"Dancing Script",cursive;font-weight:600;font-size:28px;color:var(--white)}
.back-footer{left:0;top:638px;width:480px;height:40px;background:var(--orange-soft);color:var(--white);text-align:center;font-size:9.4px;line-height:13.5px;padding-top:6px}
.back-footer b{font-weight:700}
.back-footer i{font-style:italic;opacity:.9}
</style>
</head>
<body>

<section class="page page--front" aria-label="Page 1 – Information Session">
  <div class="abs hero" role="img" aria-label="Photo of blue sky with clouds over green mountain ranges"></div>
  <div class="abs hero-band"></div>

  <h1>
    <span class="abs title title--a">QUIET</span>
    <span class="abs title title--b">PATHFINDER</span>
    <span class="abs title title--c">COURSE</span>
  </h1>
  <div class="abs session-tag">INFORMATION SESSION</div>
  <div class="abs when when--date">THURSDAY 5TH SEPTEMBER 2019</div>
  <div class="abs when when--time">19:30 TO 21:00</div>

  <div class="abs col-info">
    <h2 class="h-section h-section--orange">INFORMATION SESSION</h2>
    <p>The purpose of this <b>Information Session</b> is to give you a real insight into the Quiet Pathfinder Course and how it can help you get the most out of your work and life.</p>
  </div>
  <div class="abs col-who">
    <h2 class="h-section h-section--blue">WHO CAN COME</h2>
    <p>The Information Session is free. Whether you come on your own, or with friends or family, you'll be warmly welcome. It will take place on <b>Thursday the 5th September 2019, from 19:30 to 21:00, at KORU Coworking</b>. Please get in touch for more info or to book a place.</p>
  </div>

  <div class="abs facilitator"><span class="role">Facilitator:</span> <span class="name">DR TOMAS VERANO</span> <span class="post">Visiting Research Fellow, University of Harwick</span></div>
  <div class="abs bio-box"></div>
  <div class="abs portrait" role="img" aria-label="Portrait photo of the facilitator in a dark jacket and scarf"></div>
  <div class="abs bio-text">
    <p>Tomas joined the University of Harwick (School of Management) as a Lecturer in Entrepreneurship in 2015. He completed his PhD in Entrepreneurship at Kelbrook Business School in 2014. His work received the Lindqvist Doctoral Dissertation Award from the Academy of Enterprise Studies. He began his business career as a production engineer (Voltrex), and continued in sales (Halvorsen). After his MBA, he worked as a strategy consultant at Braga Business School. Originally from Portugal, Tomas enjoys designing and launching new ideas, international communities, mindfulness retreats, and musical improvisation. He nurtures a close connection to Willow Hollow Mindfulness Centre, where he has practiced and volunteered over 9 months. He has a broad experience of sharing the benefits of mindfulness with others.</p>
  </div>
  <div class="abs link-bar">More about the facilitator: <em>www.profiles.example/tverano</em></div>

  <div class="abs brand brand--front">
    <span class="brand-dot"></span>
    <span class="brand-name">bright<br>meadow</span>
  </div>
  <div class="abs divider"></div>
  <div class="abs booking">
    <h3>INFORMATION &amp; BOOKING</h3>
    <div class="contact-row"><span>hello@brightmeadow.example</span><span>+34 600 410 275</span></div>
    <div class="note">(video call and chat)</div>
    <div class="venue"><b>Venue:</b> KORU Coworking, C/ Olivera 12, Barcelona</div>
  </div>
</section>

<section class="page page--back" aria-label="Page 2 – About the Course">
  <div class="abs brand brand--back">
    <span class="brand-dot"></span>
    <span class="brand-name">bright<br>meadow</span>
  </div>

  <div class="abs what-band">
    <h2>What is Quiet Pathfinding</h2>
    <p>Being mindful means being aware and awake. Entrepreneurship is the creation of a new form of organising. <b>Quiet Pathfinding</b> is then the process of creating or redesigning your work and life with awareness, in a way that is reflective of you, of your passions and values, thus conducing to a greater sense of fulfilment and happiness.</p>
  </div>

  <svg class="abs cycle" viewBox="0 120 260 180" aria-label="Cycle of four workshops joined by weekly peer support meetings">
    <circle cx="129" cy="209" r="52" fill="none" stroke="#e9e9e9" stroke-width="9"/>
    <g stroke-width="2.4" fill="none">
      <path d="M100 168 h6 v8" stroke="#444"/>
      <path d="M158 176 v6 h-8" stroke="var(--green)"/>
      <path d="M150 246 v-6 h8" stroke="var(--blue)" transform="translate(6 0)"/>
      <path d="M104 242 h-6 v8" stroke="var(--orange)"/>
    </g>
    <g font-family="Roboto,sans-serif" text-anchor="middle" fill="#fff">
      <circle cx="129" cy="157" r="27" fill="var(--green)"/>
      <text x="129" y="153" font-size="6.6">Workshop 1</text>
      <text x="129" y="161" font-size="6.6">-INSIGHT-</text>
      <text x="129" y="169" font-size="6.6" font-style="italic" font-weight="700">(5 hours)</text>
      <circle cx="181" cy="209" r="27" fill="var(--blue)"/>
      <text x="181" y="205" font-size="6.6">Workshop 2</text>
      <text x="181" y="213" font-size="6.6">-DESIGN-</text>
      <text x="181" y="221" font-size="6.6" font-style="italic" font-weight="700">(3 hours)</text>
      <circle cx="129" cy="261" r="27" fill="var(--orange)"/>
      <text x="129" y="257" font-size="6.6">Workshop 3</text>
      <text x="129" y="265" font-size="6.6">-EXECUTE-</text>
      <text x="129" y="273" font-size="6.6" font-style="italic" font-weight="700">(5 hours)</text>
      <circle cx="78" cy="209" r="27" fill="var(--grey)"/>
      <text x="78" y="205" font-size="6.6">Workshop 4</text>
      <text x="78" y="213" font-size="6.6">-PRESENT-</text>
      <text x="78" y="221" font-size="6.6" font-style="italic" font-weight="700">(5 hours)</text>
    </g>
    <g font-family="Roboto,sans-serif" font-size="6.8" font-weight="500" fill="#111" text-anchor="middle">
      <text x="55" y="156">WPS Meetings</text>
      <text x="208" y="151">Weekly Peer Support</text>
      <text x="208" y="159">(WPS) meetings</text>
      <text x="208" y="167">(2 hours/week)</text>
      <text x="55" y="261">WPS Meetings</text>
      <text x="210" y="261">WPS Meetings</text>
    </g>
  </svg>

  <div class="abs program">
    <h2 class="h-block">The Program</h2>
    <p><b>The Quiet Pathfinder Course</b> is a <b>4-month long transformative journey</b> designed for people who feel stuck or not entirely satisfied with their work and/or life. It is of benefit for everyone, at any stage.</p>
    <p>The Program consists of a 5-hour workshop each month, with 2-hour weekly peer support meetings. It combines mindfulness techniques, design thinking methodology, and entrepreneurship frameworks.</p>
  </div>

  <div class="abs why">
    <h2 class="h-block">Why</h2>
    <p>Many people are not satisfied with their work, but they don't know what to do about it. This Program offers you a safe place to conduct your inner journey with collective support, helping you reflect, design, and (very likely) do something about it. It aims at:</p>
    <ul class="steps steps--why">
      <li><span class="num">1</span>Increasing awareness, clarity and confidence</li>
      <li><span class="num">2</span>Having a deeper <b><i>insight</i></b> on what makes you happier and what you want</li>
      <li><span class="num">3</span>Developing a clear <b><i>design</i></b> integrating your intended work and life</li>
      <li><span class="num">4</span>Start <b><i>executing</i></b> this design.</li>
    </ul>
  </div>

  <div class="abs how">
    <h2 class="h-block">How</h2>
    <p style="text-align:left">This Program differs from existing entrepreneurial programs in many ways:</p>
    <ul class="steps steps--how">
      <li><span class="num">1</span>Uses mindfulness and self analysis to look deeply into yourself</li>
      <li><span class="num">2</span>Design and execution decisions are based on happiness rather than (only) financials</li>
      <li><span class="num">3</span>Holistic and inclusive design process, integrating work and life, and building synergies</li>
    </ul>
    <p class="format">Format includes: lectures, individual work, group sharing, guided activities, experiential exercises, video, audio, handouts and other resources.</p>
  </div>

  <div class="abs forest" role="img" aria-label="Photo of a person walking down a long path through a pine forest"></div>
  <div class="abs motto">“The Way Out is ‘In’”</div>
  <div class="abs back-footer">
    <div><b>Email:</b> hello@brightmeadow.example</div>
    <div><b>Tel:</b> +34 600 410 275 <i>(video call and chat)</i></div>
  </div>
</section>

</body>
</html>
```